Bramwell Policy Lookout Hub

I want a landing page for them to click on the logo with a brief description of the site.

Once they click on the logo, it will take them to make a decision for two types of insurance. One will be health and the other will be home/auto.

I will need an iframe for the home/auto and it will take them to a site (which is already built) for them to get a quote.

I will need a separate iframe for the health to take them to separate site (which is built) for them to get a quote.

Target Market(s)

18-45 Year olds who want to go online for insurance quotes. This is for quoting primarily and not an information site.

Industry/Entity Type

Health

Requirements
Must have
• Sleek and sexy. I have a logo as well.

May want the following on the landing page:
Georgia's FIRST Insurance Exchange for Home, Auto, and Health Insurance

No Hassle, Real-time, Quotes - As a Matter of fact... You call us if interested, We dont sell your information and Most Importantly… its free!!

Give it a shot… Click on the logo to get started and if you are interested in one of the many carriers we represent, call us.
Should not have
• Don't want the typical website. I want this to be different than all template boxes.

```html
<!DOCTYPE html>
<html lang="en">
<head>
<meta charset="utf-8">
<title>Bramwell Policy Lookout Hub</title>
<link rel="stylesheet" href="https://fonts.googleapis.com/css2?family=Oswald:wght@400;500;600&family=Roboto+Condensed:wght@400&family=Open+Sans:wght@400&display=swap">
<style>
  :root {
    --nav-red-top: #d0172f;
    --nav-red-bottom: #86091c;
    --nav-divider: #e0354b;
    --sand-top: #f7d592;
    --sand-bottom: #c78c56;
    --footer-top: #0c2532;
    --footer-bottom: #1f4b5f;
    --card: #ffffff;
    --headline: #1db4e9;
    --label-red: #c8102e;
    --brand-dark: #2a2a2a;
    --spine: #e2a65c;
    --ring: #5d5d5d;
    --icon-yellow: #ffc70a;
    --icon-ring: #d9d9d9;
  }
  * { margin: 0; padding: 0; box-sizing: border-box; }
  html, body { width: 1200px; height: 673px; overflow: hidden; }
  body {
    position: relative;
    background: linear-gradient(180deg, var(--sand-top) 0%, var(--sand-bottom) 100%);
    font-family: "Open Sans", sans-serif;
  }
  .site-nav {
    position: absolute; left: 0; top: 0; width: 1200px; height: 78px;
    background: linear-gradient(180deg, var(--nav-red-top), var(--nav-red-bottom));
    display: flex;
  }
  .site-nav a {
    display: flex; align-items: center; height: 78px;
    color: #fff; text-decoration: none;
    font-family: "Oswald", sans-serif; font-weight: 500; font-size: 25px;
    letter-spacing: 0.2px; text-transform: uppercase;
    border-right: 1px solid var(--nav-divider);
  }
  .site-nav a.nav-home { width: 156px; padding-left: 22px; }
  .site-nav a.nav-quote { width: 222px; padding-left: 42px; }
  .site-nav a.nav-contact { border-right: none; padding-left: 38px; }

  .card {
    position: absolute; top: 168px; height: 332px;
    background: var(--card); border-radius: 46px;
    box-shadow: 0 4px 8px rgba(60, 30, 0, 0.45);
  }
  .card-brand { left: 12px; width: 365px; }
  .card-choices { left: 386px; width: 802px; }

  .brand-name {
    position: absolute; left: 0; top: 0; width: 100%; height: 100%;
    display: flex; flex-direction: column; align-items: center; justify-content: center; gap: 18px;
  }
  .brand-mark { width: 70px; height: 70px; border-radius: 50%; background: var(--label-red); }
  .brand-text {
    font-family: "Oswald", sans-serif; font-weight: 600; font-size: 40px; line-height: 1.1;
    color: var(--brand-dark); text-align: center; text-transform: uppercase;
  }

  .binding { position: absolute; left: 340px; top: 200px; }

  .headline {
    position: absolute; left: 0; top: 30px; width: 100%; text-align: center;
    font-family: "Oswald", sans-serif; font-weight: 600; font-size: 37px;
    color: var(--headline); text-transform: uppercase;
    text-shadow: 0 2px 2px rgba(0, 60, 90, 0.35);
  }
  .choice { position: absolute; top: 112px; width: 220px; text-align: center; text-decoration: none; }
  .choice-home { left: 51px; }
  .choice-auto { left: 309px; }
  .choice-life { left: 564px; }
  .choice-icon {
    display: block; margin: 0 auto; width: 140px; height: 140px; border-radius: 50%;
    border: 7px solid #fff; box-shadow: 0 0 0 3px var(--icon-ring), 0 3px 6px rgba(0,0,0,0.3);
    background: radial-gradient(circle at 50% 70%, #d4233c 0%, var(--icon-yellow) 75%);
  }
  .choice-auto .choice-icon { background: linear-gradient(180deg, var(--icon-yellow) 45%, #3c7cc9 80%); }
  .choice-life .choice-icon { background: radial-gradient(circle at 50% 60%, #ffffff 0%, var(--icon-yellow) 55%); }
  .choice-label {
    display: block; margin-top: 20px;
    font-family: "Roboto Condensed", sans-serif; font-size: 25px;
    color: var(--label-red); text-transform: uppercase;
  }

  .site-footer {
    position: absolute; left: 0; top: 610px; width: 1200px; height: 63px;
    background: linear-gradient(180deg, var(--footer-top), var(--footer-bottom));
    display: flex; align-items: center; justify-content: center;
    color: #fff; font-size: 17px; white-space: pre;
  }
</style>
</head>
<body>
  <nav class="site-nav">
    <a class="nav-home" href="#">Home Page</a>
    <a class="nav-quote" href="#">Quote Request</a>
    <a class="nav-contact" href="#">Contact Us</a>
  </nav>

  <section class="card card-brand">
    <div class="brand-name">
      <span class="brand-mark"></span>
      <span class="brand-text">Bramwell Policy<br>Lookout Hub</span>
    </div>
  </section>

  <svg class="binding" width="80" height="270" viewBox="0 0 80 270" aria-hidden="true">
    <rect x="39" y="0" width="4" height="270" fill="var(--spine)"/>
    <g fill="none" stroke="var(--ring)" stroke-width="5">
      <ellipse cx="40" cy="22" rx="24" ry="7"/>
      <ellipse cx="40" cy="66" rx="24" ry="7"/>
      <ellipse cx="40" cy="111" rx="24" ry="7"/>
      <ellipse cx="40" cy="156" rx="24" ry="7"/>
      <ellipse cx="40" cy="200" rx="24" ry="7"/>
      <ellipse cx="40" cy="246" rx="24" ry="7"/>
    </g>
  </svg>

  <section class="card card-choices">
    <h1 class="headline">Just click any logo to get started</h1>
    <a class="choice choice-home" href="#">
      <span class="choice-icon" role="img" aria-label="Illustration of a house"></span>
      <span class="choice-label">Home Insurance</span>
    </a>
    <a class="choice choice-auto" href="#">
      <span class="choice-icon" role="img" aria-label="Illustration of a car on a road"></span>
      <span class="choice-label">Auto Insurance</span>
    </a>
    <a class="choice choice-life" href="#">
      <span class="choice-icon" role="img" aria-label="Illustration of a person silhouette"></span>
      <span class="choice-label">Life Insurance</span>
    </a>
  </section>

  <footer class="site-footer">© 2013, All Rights Reserved,  Bramwellhub.com</footer>
</body>
</html>
```